Business Card Design

I already have a company logo for my company. I have a logo for the manufacturer we represent. I want a professional business card design.

```html
<!DOCTYPE html>
<html lang="en">
<head>
<meta charset="utf-8">
<title>Beacon Alert Group – Business Card</title>
<link rel="stylesheet" href="https://fonts.googleapis.com/css2?family=Open+Sans:wght@400;600;700&display=swap">
<style>
  :root {
    --stage: #2e2e2e;
    --card: #151515;
    --red: #e3252b;
    --white: #f2f2f2;
    --muted: #d8d8d8;
  }
  * { box-sizing: border-box; margin: 0; padding: 0; }
  html, body {
    width: 1200px; height: 780px; overflow: hidden;
    background: var(--stage);
    font-family: "Open Sans", Arial, sans-serif;
  }
  .stage {
    position: relative; width: 1200px; height: 780px;
    display: flex; align-items: center; justify-content: center; gap: 60px;
  }
  .card {
    position: relative; width: 520px; height: 297px;
    background: var(--card); border-radius: 18px; overflow: hidden;
  }

  /* Front */
  .brand-small {
    position: absolute; left: 34px; top: 30px;
    display: flex; align-items: center; gap: 8px;
    font-weight: 700; font-size: 15px; letter-spacing: 1px;
    color: var(--white); text-transform: uppercase;
  }
  .brand-dot { width: 10px; height: 10px; border-radius: 50%; background: var(--red); }
  .address {
    position: absolute; left: 34px; top: 84px;
    font-size: 12px; line-height: 18px; color: var(--muted);
  }
  .contacts {
    position: absolute; left: 34px; top: 136px;
    list-style: none; font-size: 12px; line-height: 19px; color: var(--white);
  }
  .contacts li { display: flex; align-items: center; gap: 7px; }
  .contacts svg { width: 10px; height: 10px; fill: var(--red); flex: none; }
  .brand-large {
    position: absolute; right: 42px; top: 92px;
    font-weight: 700; font-size: 26px; letter-spacing: 1.5px;
    color: var(--white); text-transform: uppercase; text-align: right; line-height: 30px;
  }
  .person {
    position: absolute; right: 40px; bottom: 34px; text-align: right;
  }
  .person-name {
    font-weight: 600; font-size: 19px; letter-spacing: 0.5px;
    color: var(--red); text-transform: uppercase;
  }
  .person-role { font-size: 13px; color: var(--white); }
  .edge-bar {
    position: absolute; right: 0; bottom: 26px; width: 10px; height: 62px; background: var(--red);
  }

  /* Back */
  .card-back { display: flex; align-items: center; justify-content: center; }
  .brand-centre {
    display: flex; align-items: center; gap: 12px;
    font-weight: 700; font-size: 30px; letter-spacing: 2px;
    color: var(--white); text-transform: uppercase;
  }
  .brand-centre .brand-dot { width: 16px; height: 16px; }
</style>
</head>
<body>
<main class="stage">
  <section class="card card-front">
    <div class="brand-small"><span class="brand-dot"></span>Beacon Alert Group</div>
    <p class="address">Your address, City<br>State, Zip 1234</p>
    <ul class="contacts">
      <li><svg viewBox="0 0 10 10" aria-hidden="true"><path d="M2 0.5 L3.8 2.6 L2.9 3.8 Q4 6 6.2 7.1 L7.4 6.2 L9.5 8 L8.3 9.5 Q4.5 9.4 2.5 7.5 Q0.6 5.5 0.5 1.7 Z"/></svg>123 456 789</li>
      <li><svg viewBox="0 0 10 10" aria-hidden="true"><path d="M0.5 2 H9.5 V8.5 H0.5 Z M1.2 2.6 L5 5.6 L8.8 2.6 Z" fill-rule="evenodd"/></svg>info@beaconalert.com</li>
      <li><svg viewBox="0 0 10 10" aria-hidden="true"><circle cx="5" cy="5" r="4.5"/></svg>www.beaconalert.com</li>
    </ul>
    <div class="brand-large">Beacon Alert<br>Group</div>
    <div class="person">
      <p class="person-name">Daniel Reyes</p>
      <p class="person-role">Managing Director</p>
    </div>
    <span class="edge-bar"></span>
  </section>

  <section class="card card-back">
    <div class="brand-centre"><span class="brand-dot"></span>Beacon Alert Group</div>
  </section>
</main>
</body>
</html>
```